Brookvale Building Company - advertisement poster

I am looking to print some canvas signs to advertise my general contracting company, Brookvale Building Company. The sign will measure 6' long x 3' high so the size should match that ratio. I already have a logo icon, which is the Letter 'B' and some trees that I would like to incorporate, see attached. I would also like the to have the following information listed:
1) phone number: 831-555-0172
2) email: brookvalebuildingcompany@mailnest.example
3) website: brookvalebuildingcompany.example
4) Lic#4826130
5) I want to use this text: "BUILD WITH THE B-CREW!"

The ad should be relatively simple and clean. Black and Green are my company colors. I am open to creative ideas!

Target Market(s)

People looking to renovate their homes

Industry/Entity Type

Construction

Colors
59FF00
82FF00
B8FF75
E3FFCB
F4FFEA

Requirements
Must have
• Must have my company logo
Should not have
• No photos or complex graphics

```html
<!DOCTYPE html>
<html lang="en">
<head>
<meta charset="utf-8">
<title>Brookvale Building Company – Sign</title>
<link rel="stylesheet" href="https://fonts.googleapis.com/css2?family=Bebas+Neue&family=Michroma&family=Montserrat:wght@300;400;600;800&display=swap">
<style>
  :root{
    --page:#bbeb9c;
    --green:#70b548;
    --green-dark:#53992c;
    --green-deep:#324f21;
    --black:#000000;
    --white:#ffffff;
    --ground:#2e2e2e;
  }
  *{margin:0;padding:0;box-sizing:border-box}
  html,body{width:1200px;height:663px;overflow:hidden;background:var(--page)}
  .canvas{position:relative;width:1200px;height:663px}
  .artwork{position:absolute;left:0;top:0}
  .abs{position:absolute}

  .estd,.year{font-family:"Michroma",sans-serif;color:var(--white);font-size:10px;letter-spacing:4px;top:282px;
    border-top:1px solid var(--green);border-bottom:1px solid var(--green);padding:3px 0 3px 2px;text-align:center}
  .estd{left:158px;width:52px}
  .year{left:400px;width:52px}
  .brand-mark{left:273px;top:232px;width:64px;height:64px;background:var(--green)}

  .brand-name{left:140px;top:322px;width:330px;text-align:center;font-family:"Michroma",sans-serif;
    font-size:36px;line-height:1;color:var(--white);letter-spacing:1px}
  .brand-sub{left:140px;top:366px;width:330px;text-align:center;font-family:"Michroma",sans-serif;
    font-size:15px;line-height:1;color:var(--green);letter-spacing:5.4px}
  .licence{left:229px;top:398px;width:153px;height:37px;border:3px solid var(--green);border-radius:14px;
    display:flex;align-items:center;justify-content:center;font-family:"Montserrat",sans-serif;font-weight:400;
    font-size:18px;color:var(--white)}

  .sign-illustration{left:572px;top:137px;width:504px;height:287px;border-radius:6px;
    background:linear-gradient(180deg,var(--green) 0%,var(--green) 70%,var(--ground) 100%)}

  .slogan{font-family:"Bebas Neue",sans-serif;line-height:.8}
  .slogan-build{left:716px;top:204px;font-size:86px;color:var(--white)}
  .slogan-with{left:870px;top:208px;font-size:38px;color:var(--black);line-height:.82}
  .slogan-crew{left:724px;top:274px;font-size:80px;color:var(--black);letter-spacing:1px}

  .phone-number{left:712px;top:438px;font-family:"Montserrat",sans-serif;font-weight:800;font-size:49px;
    line-height:1;color:var(--green);letter-spacing:-1px}

  .contact{font-family:"Montserrat",sans-serif;font-weight:600;color:var(--black);line-height:1;
    padding-bottom:3px;border-bottom:2px solid var(--black);top:534px;text-transform:uppercase}
  .contact-web{left:470px;font-size:10.8px}
  .contact-mail{left:779px;font-size:10px}
</style>
</head>
<body>
<div class="canvas">
  <svg class="artwork" width="1200" height="663" viewBox="0 0 1200 663" aria-hidden="true">
    <rect x="99" y="77" width="1003" height="509" fill="var(--green)"/>
    <rect x="107" y="85" width="986" height="493" fill="var(--black)"/>
    <polygon points="382,510 1093,510 1093,578 304,578" fill="var(--green)"/>
    <polygon points="311,85 334,85 576,313 565,321" fill="var(--green-deep)"/>
    <polyline points="304,85 574,332 304,578" fill="none" stroke="var(--green)" stroke-width="3"/>
    <circle cx="660" cy="462" r="34" fill="none" stroke="var(--green)" stroke-width="4"/>
    <path d="M647,446 l6,-3 l5,10 l-4,4 q3,8 11,12 l4,-4 l10,5 l-3,6 q-4,3 -10,1 q-17,-8 -22,-22 q-1,-6 3,-9z" fill="var(--green)"/>
    <path d="M668,446 a9,9 0 0 1 9,9 M668,439 a16,16 0 0 1 16,16" fill="none" stroke="var(--green)" stroke-width="2.5" stroke-linecap="round"/>
    <circle cx="439" cy="541" r="14" fill="var(--black)"/>
    <circle cx="438" cy="540" r="7" fill="none" stroke="var(--green)" stroke-width="1.2"/>
    <path d="M431,540 h14 M438,533 v14 M434,535 q4,5 0,10 M442,535 q-4,5 0,10" fill="none" stroke="var(--green)" stroke-width="1"/>
    <circle cx="750" cy="541" r="16" fill="var(--black)"/>
    <rect x="742" y="535" width="16" height="11" fill="none" stroke="var(--green)" stroke-width="1.3"/>
    <path d="M742,535 l8,6 l8,-6" fill="none" stroke="var(--green)" stroke-width="1.3"/>
  </svg>

  <div class="abs estd">ESTD</div>
  <div class="abs brand-mark" aria-hidden="true"></div>
  <div class="abs year">2020</div>
  <div class="abs brand-name">BROOKVALE</div>
  <div class="abs brand-sub">BUILDING COMPANY</div>
  <div class="abs licence">LIC#4826130</div>

  <div class="abs sign-illustration" role="img" aria-label="Illustration of a green house-shaped sign with a hammer, standing on a dark round platform"></div>
  <div class="abs slogan slogan-build">BUILD</div>
  <div class="abs slogan slogan-with">WITH<br>THE</div>
  <div class="abs slogan slogan-crew">B-CREW!</div>

  <div class="abs phone-number">831-555-0172</div>
  <div class="abs contact contact-web">brookvalebuildingcompany.example</div>
  <div class="abs contact contact-mail">brookvalebuildingcompany@mailnest.example</div>
</div>
</body>
</html>
```